Redesign of LumoWordfind.com in Bootstrap 4

Current design of LumoWordfind.com is not responsive. We need to change it to latest version of Bootstrap 4 keeping essential elements in place.

Apart from home page, we need designs for http://www.lumowordfind.com/meaning/cat also.

Coding

Number of Pages Required

2 page

Colors
34a7d8

Requirements
Must have
• Bootstrap 4

```html
<!DOCTYPE html>
<html lang="en">
<head>
<meta charset="utf-8">
<title>Lumo Wordfind</title>
<link href="https://fonts.googleapis.com/css2?family=Ubuntu:wght@400;500;700&display=swap" rel="stylesheet">
<style>
:root{
  --teal:#1698b0;
  --teal-dark:#0d6f80;
  --blue:#34a7d8;
  --footer:#2e9fd5;
  --orange:#f7941d;
  --green:#2a8a1f;
  --navy:#1e3f66;
  --grey-band:#e5e6e7;
  --text:#444;
  --line:#dcdcdc;
}
*{box-sizing:border-box;margin:0;padding:0}
html,body{width:821px;height:1200px;overflow:hidden}
body{position:relative;font-family:"Ubuntu",sans-serif;color:var(--text);background:#fff}
.abs{position:absolute}
.site-header{left:0;top:0;width:821px;height:410px;background:var(--teal)}
.brand{left:52px;top:34px;color:#fff;font-weight:700;font-size:26px;line-height:26px}
.brand small{display:block;font-size:10px;line-height:12px;font-weight:500;letter-spacing:.5px}
.btn-login{left:644px;top:13px;width:55px;height:25px;background:var(--blue);color:#fff;font-size:10px;display:flex;align-items:center;justify-content:center}
.btn-join{left:709px;top:13px;width:61px;height:25px;border:1.5px solid #fff;color:#fff;font-size:10px;display:flex;align-items:center;justify-content:center}
.main-nav{left:331px;top:52px;display:flex;gap:0;font-size:12px;color:#fff}
.main-nav span{padding:6px 12px;margin-right:7px}
.main-nav .active{background:var(--orange)}
.nav-rule{left:51px;top:89px;width:719px;height:1px;background:rgba(255,255,255,.3)}
.hero-art{left:0;top:120px;width:821px;height:290px;background:linear-gradient(90deg,#1ba3b8,#3b9bb5 40%,#e9d4b7 55%,#1fa0b6 70%,#dfe6ea)}
.search-panel{left:164px;top:154px;width:493px;height:94px;background:rgba(10,90,105,.85)}
.search-title{left:164px;top:158px;width:493px;text-align:center;color:#fff;font-size:28px;font-weight:500}
.search-input{left:174px;top:206px;width:369px;height:30px;background:#fff;border:1px solid #ccc;font-size:9px;padding:10px;color:#555}
.search-btn{left:555px;top:205px;width:92px;height:31px;background:linear-gradient(#3aa628,#1f7a14);color:#fff;font-size:18px;font-weight:500;display:flex;align-items:center;justify-content:center}
.ad-banner{left:52px;top:443px;width:459px;height:57px;background:linear-gradient(90deg,#2d5f9a,#5d6f3a 40%,#7a5d2a 70%,#3d3d3d);border:1px solid #444}
.wotd{left:543px;top:423px;width:227px;height:96px;border:1px solid var(--line)}
.wotd-head{background:var(--blue);color:#fff;font-size:12px;font-weight:500;padding:6px 10px;height:24px}
.wotd-word{text-align:center;font-size:16px;color:#333;margin-top:10px}
.wotd-phon{text-align:center;font-size:8px;color:#666;font-style:italic;margin-top:2px}
.wotd-foot{position:absolute;left:0;bottom:0;width:100%;height:22px;background:#f1f1f1;font-size:9px;color:#2a7bb5;padding:6px 10px;text-align:right}
.wotd-foot i{position:absolute;top:7px;width:9px;height:9px;border-radius:50%;background:#333}
.browse-bar{left:0;top:528px;width:821px;height:40px;background:var(--grey-band);display:flex;align-items:center;font-size:9px}
.browse-bar b{color:var(--navy);font-weight:700;margin-left:51px;width:115px}
.browse-bar span{width:23.9px;text-align:center;border-left:1px solid #d2d2d2;height:40px;line-height:40px;color:#333}
.feature-head{left:51px;top:594px;color:var(--blue);font-size:14px;font-weight:700}
.feature-list{left:51px;top:624px;list-style:none;font-size:9.5px;color:#333}
.feature-list li{height:22px;display:flex;align-items:center}
.feature-list li::before{content:"";width:9px;height:9px;border-radius:50%;background:var(--blue);margin-right:9px}
.btn-register{left:51px;top:721px;width:132px;height:32px;background:linear-gradient(#2c9a1e,#1d7512);color:#fff;font-weight:700;font-size:12px;display:flex;align-items:center;justify-content:center}
.feature-art{left:385px;top:596px;width:385px;height:158px;background:linear-gradient(135deg,#5c7e93,#a9c2d2 50%,#dbe5ea 70%,#8fa9ba)}
.section-rule{left:51px;top:782px;width:719px;height:1px;background:var(--line)}
.card{top:807px;width:166px;height:215px;border:1px solid var(--line);background:#f7f7f7;text-align:center;padding-top:16px}
.card .icon{width:60px;height:60px;border-radius:50%;background:var(--blue);margin:0 auto;display:flex;align-items:center;justify-content:center}
.card h3{color:var(--blue);font-size:12.5px;font-weight:500;margin-top:15px}
.card .sub{color:var(--green);font-size:9.5px;font-weight:500;margin-top:3px}
.card p{font-size:8.5px;color:#333;line-height:16px;margin:3px 14px 0}
.card .cta{display:inline-block;background:var(--orange);color:#fff;font-size:8.5px;padding:5px 10px;margin-top:7px}
.site-footer{left:0;top:1052px;width:821px;height:148px;background:var(--footer);color:#fff}
.foot-brand{left:52px;top:30px;font-weight:700;font-size:26px;line-height:26px}
.foot-brand small{display:block;font-size:10px;line-height:12px;font-weight:500}
.copy{left:52px;top:84px;font-size:8px;line-height:16px}
.foot-col{top:30px;font-size:8px;line-height:16px}
.foot-col h4{font-size:9.5px;font-weight:500;margin-bottom:2px}
.social{left:628px;top:50px;display:flex;gap:8px}
.social i{width:20px;height:20px;border-radius:50%;background:#1d5f98}
.social i:nth-child(2){background:#2a8fd0}
.social i:nth-child(3){background:#1a7db6}
.social i:nth-child(4){background:#444}
.social i:nth-child(5){background:#f7941d}
</style>
</head>
<body>
<header class="site-header abs">
  <div class="hero-art abs" role="img" aria-label="Flat illustration of a desk with coffee, open book, tablet, notebooks and a laptop"></div>
  <div class="brand abs">Lumo<small>WORDFIND</small></div>
  <div class="btn-login abs">Log In</div>
  <div class="btn-join abs">Join Free</div>
  <nav class="main-nav abs"><span class="active">Home</span><span>Idioms</span><span>Common Errors</span><span>Crossword</span><span>Blog</span><span>Contact</span></nav>
  <div class="nav-rule abs"></div>
  <div class="search-panel abs"></div>
  <div class="search-title abs">Lumo English Wordfind</div>
  <div class="search-input abs">Enter a Word,or Phrase</div>
  <div class="search-btn abs">Search</div>
</header>

<div class="ad-banner abs" role="img" aria-label="Web hosting advertisement banner"></div>

<aside class="wotd abs">
  <div class="wotd-head">WORD OF THE DAY</div>
  <div class="wotd-word">exhaustive</div>
  <div class="wotd-phon">/ɪɡˈzɔːstɪv/</div>
  <div class="wotd-foot"><i style="left:10px"></i><i style="left:28px;background:#555"></i>Show Defination</div>
</aside>

<div class="browse-bar abs"><b>BROWSE DICTIONARY:</b><span>A</span><span>B</span><span>C</span><span>D</span><span>E</span><span>F</span><span>G</span><span>H</span><span>I</span><span>J</span><span>K</span><span>L</span><span>M</span><span>N</span><span>O</span><span>P</span><span>Q</span><span>R</span><span>S</span><span>T</span><span>U</span><span>V</span><span>W</span><span>X</span><span>Y</span><span>Z</span></div>

<h2 class="feature-head abs">SEARCH, SAVE AND MASTER WORDS</h2>
<ul class="feature-list abs">
  <li>Search from more than 300,000 words and phrases</li>
  <li>Multiple usages to clarify the context</li>
  <li>Audio, phonetics, meanings, synonyms and antonyms</li>
  <li>Save the words to your personal deck and access from anywhere</li>
</ul>
<div class="btn-register abs">REGISTER FREE</div>
<div class="feature-art abs" role="img" aria-label="Photo of a hand holding an open book with letters flying into a cloudy sky"></div>
<div class="section-rule abs"></div>

<div class="card abs" style="left:51px">
  <div class="icon"><svg width="26" height="22"><rect x="1" y="1" width="24" height="20" rx="2" fill="none" stroke="#fff" stroke-width="1.5"/><text x="13" y="16" fill="#fff" font-size="11" font-family="Ubuntu,sans-serif" text-anchor="middle">Aa</text></svg></div>
  <h3>English Tidbit</h3>
  <div class="sub">gaffe/gaff</div>
  <p>"Gaffe" is a social blunder and "gaff" is a large hook. Be warned not to make the gaffe of mixing it up with gaff.</p>
</div>
<div class="card abs" style="left:236px">
  <div class="icon"><svg width="28" height="24"><rect x="2" y="7" width="24" height="11" rx="2" fill="#fff"/><rect x="7" y="2" width="14" height="6" fill="#fff"/><rect x="8" y="14" width="12" height="8" fill="#fff" stroke="#34a7d8"/></svg></div>
  <h3>Daily Crossword</h3>
  <p>Crossword Lovers!<br>Take this daily crossword challenge from Lumo Wordfind.</p>
  <span class="cta">Slove it Now</span>
</div>
<div class="card abs" style="left:420px">
  <div class="icon"><svg width="28" height="28"><path d="M4 10h6a3 3 0 1 1 6 0h6v6a3 3 0 1 0 0 6v4H4z" fill="#fff"/></svg></div>
  <h3>Browser Addon</h3>
  <p>Add this tool to your Kestrel Browser and quickly look up for definitions from any website without leaving the page.</p>
  <span class="cta">Get it Now</span>
</div>
<div class="card abs" style="left:605px">
  <div class="icon"><svg width="18" height="28"><rect x="1" y="1" width="16" height="26" rx="3" fill="#fff"/><rect x="3" y="5" width="12" height="16" fill="#34a7d8"/></svg></div>
  <h3>Designed for Phone</h3>
  <p>Lumo Wordfind is specially designed for your Pomelo phone to quickly lookup meaining, usages and audio of words.</p>
</div>

<footer class="site-footer abs">
  <div class="foot-brand abs">Lumo<small>WORDFIND</small></div>
  <div class="copy abs">Copyright © 2016 Company Name.<br>All Rights Reserved.</div>
  <div class="foot-col abs" style="left:234px"><h4>LumoWordfind.com</h4>FAQ<br>Contact<br>Blog</div>
  <div class="foot-col abs" style="left:360px"><h4>Legal</h4>Privacy Policy<br>Terms of Use</div>
  <div class="foot-col abs" style="left:481px"><h4>Others</h4>Popular Words<br>Common Errors in English<br>Exam Prep Online</div>
  <div class="foot-col abs" style="left:628px"><h4>Connect Us</h4></div>
  <div class="social abs"><i></i><i></i><i></i><i></i><i></i></div>
</footer>
</body>
</html>
```